Melorix artwork for new single release

I need Melorix artwork creating to release a new single on there.

The specs are:

Ideal size: 3000 x 3000 pixels
Minimum size: 1400 x 1400 pixels
Aspect ratio: 1:1 (must be a perfect square)
File format: JPG or PNG
Color space: sRGB
File size: Max 4MB

The song is called "Was It Ever Rain?"
The artist is "Martin Hollow"

We have no images of Martin, so it really is open to imagination.

Target Market(s)

Melorix listeners

Industry/Entity Type

Music

```html
<!DOCTYPE html>
<html lang="en">
<head>
<meta charset="utf-8">
<title>Was It Ever Rain? — Martin Hollow</title>
<link rel="stylesheet" href="https://fonts.googleapis.com/css2?family=Lobster&family=DM+Sans:wght@600&display=swap">
<style>
  :root {
    --paint-pink: #f2147e;
    --paint-hot: #ff1f6a;
    --paint-magenta: #c812b8;
    --paint-violet: #7a1fd6;
    --paint-blue: #2438e6;
    --ink-white: #ffffff;
  }
  html, body {
    margin: 0;
    padding: 0;
    width: 1200px;
    height: 1200px;
    overflow: hidden;
    background: var(--paint-pink);
  }
  .cover {
    position: relative;
    width: 1200px;
    height: 1200px;
    overflow: hidden;
  }
  .cover__paint {
    position: absolute;
    inset: 0;
    background:
      radial-gradient(ellipse 38% 30% at 4% 6%, var(--paint-blue) 0%, transparent 75%),
      radial-gradient(ellipse 30% 45% at 12% 35%, var(--paint-violet) 0%, transparent 80%),
      radial-gradient(ellipse 25% 40% at 95% 35%, var(--paint-violet) 0%, transparent 80%),
      radial-gradient(ellipse 30% 35% at 8% 88%, var(--paint-magenta) 0%, transparent 80%),
      radial-gradient(ellipse 45% 40% at 55% 55%, var(--paint-hot) 0%, transparent 80%),
      linear-gradient(160deg, var(--paint-magenta) 0%, var(--paint-pink) 45%, var(--paint-pink) 100%);
  }
  .cover__title {
    position: absolute;
    left: 0;
    right: 0;
    top: 150px;
    margin: 0;
    text-align: center;
    font-family: "Lobster", cursive;
    font-weight: 400;
    color: var(--ink-white);
    line-height: 1;
  }
  .cover__title span { display: block; }
  .title__lead { font-size: 150px; transform: translateX(-10px) rotate(-4deg); }
  .title__line { font-size: 210px; margin-top: -10px; transform: rotate(-4deg); }
  .title__line--last { font-size: 230px; margin-top: -5px; }
  .cover__swash {
    position: absolute;
    left: 420px;
    top: 890px;
    width: 460px;
    height: 110px;
  }
  .cover__artist {
    position: absolute;
    left: 0;
    right: 0;
    top: 1062px;
    margin: 0;
    text-align: center;
    font-family: "DM Sans", sans-serif;
    font-weight: 600;
    font-size: 50px;
    color: var(--ink-white);
  }
</style>
</head>
<body>
  <main class="cover">
    <div class="cover__paint" role="img" aria-label="Abstract fluid paint texture in hot pink, magenta and electric blue"></div>
    <h1 class="cover__title">
      <span class="title__lead">Was It</span>
      <span class="title__line">Ever</span>
      <span class="title__line title__line--last">Rain?</span>
    </h1>
    <svg class="cover__swash" viewBox="0 0 460 110" aria-hidden="true">
      <path d="M10 100 C 120 40, 300 20, 450 40 C 300 40, 140 60, 10 100 Z" fill="#ffffff"/>
    </svg>
    <p class="cover__artist">Martin Hollow</p>
  </main>
</body>
</html>
```